Business Card Design

I am a GP with interest in Dermatology and Aesthetic Medicin, performing Botulinum Toxin Type A and Dermal Fillers treatmets in Cosmetic Dermatology clinic.

I am looking for a white colour, good quality white paper card may be of some special texture with black calligraphic writing but easy to read and not to wiggly- professional- looking.

Really appreciate your help.

Marisha

Cosmetic Dermatology Clinic

Dr Marisha Volkovska, MBBS, MRCGP, DPD

Tel: 07941 586 217
marisha@medpracto.org.uk

```html
<!DOCTYPE html>
<html lang="en">
<head>
<meta charset="utf-8">
<title>Cosmetic Dermatology Clinic – Business Card</title>
<link href="https://fonts.googleapis.com/css2?family=Cormorant+Garamond:ital,wght@0,400;0,500;0,600;1,400&family=Pinyon+Script&display=swap" rel="stylesheet">
<style>
  :root{
    --backdrop:#8c8c8c;
    --paper:#fdfcf9;
    --ink:#141414;
    --ink-soft:#3a3a3a;
    --rule:#1a1a1a;
  }
  *{box-sizing:border-box;margin:0;padding:0}
  html,body{width:1200px;height:1200px;overflow:hidden}
  body{background:var(--backdrop);font-family:"Cormorant Garamond",serif;color:var(--ink);position:relative}

  .card{position:absolute;top:250px;width:400px;height:700px;background:var(--paper);
        display:flex;flex-direction:column;overflow:hidden;box-shadow:0 6px 18px rgba(0,0,0,.25)}
  .card--back{left:150px}
  .card--front{left:650px}

  .card__head{display:flex;align-items:center;justify-content:center;padding:0 28px;border-bottom:1px solid var(--rule)}
  .clinic-name{font-family:"Pinyon Script",cursive;font-weight:400;font-size:42px;line-height:1.25;text-align:center;color:var(--ink)}

  .zone{display:flex;flex-direction:column;justify-content:center;gap:16px;padding:0 26px}
  .zone + .zone{border-top:1px solid var(--rule)}

  .pill{display:flex;align-items:center;gap:14px;min-height:50px;padding:8px 14px;border:1px solid var(--ink);border-radius:6px;
        font-size:20px;font-weight:500;letter-spacing:.3px;color:var(--ink)}
  .pill--tall{font-size:18px;line-height:1.25}
  .pill__icon{flex:none;width:26px;height:26px}
  .pill__mark{flex:none;width:22px;height:22px;border:1.5px solid var(--ink);border-radius:3px}

  .person{text-align:center}
  .person__name{font-family:"Pinyon Script",cursive;font-weight:400;font-size:36px;line-height:1.2}
  .person__creds{margin-top:6px;font-size:15px;font-weight:600;letter-spacing:3px;color:var(--ink-soft)}
</style>
</head>
<body>

<section class="card card--back" aria-label="Card back">
  <div class="card__head" style="height:320px">
    <h1 class="clinic-name">Cosmetic<br>Dermatology Clinic</h1>
  </div>
  <div class="zone" style="height:380px;gap:22px">
    <div class="pill"><span class="pill__mark"></span>chatterline.net/medpracto</div>
    <div class="pill"><span class="pill__mark"></span>quickpost.net/medpracto</div>
    <div class="pill"><span class="pill__mark"></span>workcircle.net/medpracto</div>
  </div>
</section>

<section class="card card--front" aria-label="Card front">
  <div class="card__head" style="height:250px">
    <h1 class="clinic-name">Cosmetic<br>Dermatology Clinic</h1>
  </div>
  <div class="zone" style="height:140px">
    <div class="person">
      <div class="person__name">Dr Marisha Volkovska</div>
      <div class="person__creds">MBBS · MRCGP · DPD</div>
    </div>
  </div>
  <div class="zone" style="height:310px;gap:14px">
    <div class="pill">
      <svg class="pill__icon" viewBox="0 0 24 24" fill="none" stroke="#141414" stroke-width="1.6" stroke-linejoin="round"><path d="M6 3h3l2 5-2 1.5a11 11 0 0 0 5.5 5.5L16 13l5 2v3a3 3 0 0 1-3 3A15 15 0 0 1 3 6a3 3 0 0 1 3-3z"/></svg>
      07941 586 217
    </div>
    <div class="pill">
      <svg class="pill__icon" viewBox="0 0 24 24" fill="none" stroke="#141414" stroke-width="1.6" stroke-linejoin="round"><rect x="3" y="6" width="18" height="12" rx="1"/><path d="M3 7l9 6 9-6"/></svg>
      marisha@medpracto.org.uk
    </div>
    <div class="pill">
      <svg class="pill__icon" viewBox="0 0 24 24" fill="none" stroke="#141414" stroke-width="1.4"><circle cx="12" cy="12" r="9"/><ellipse cx="12" cy="12" rx="4" ry="9"/><path d="M3 12h18M5 7h14M5 17h14"/></svg>
      www.medpracto-clinic.co.uk
    </div>
    <div class="pill pill--tall">
      <svg class="pill__icon" viewBox="0 0 24 24" fill="none" stroke="#141414" stroke-width="1.6"><path d="M12 22s-7-7.5-7-12.5a7 7 0 0 1 14 0C19 14.5 12 22 12 22z"/><circle cx="12" cy="9.5" r="2.5"/></svg>
      <span>24 Linden Road, 2nd floor<br>Westfield St.</span>
    </div>
  </div>
</section>

</body>
</html>
```